website homepage design sample for tovelane.com.au

Hello, I am looking to update my website to be simpler and more modern and to include space for my upcoming online courses. Please review my website tovelane.com.au for an idea of me as a male psychologist, as well as my services. I would like it to be NOT too feminine. Target market is Men and women interested in couselling, life coaching, and online courses about relationships. Id like to keep the beach theme if possible but I am open to better ideas. thank you!

please see tovelane.com.au for my current wordpress website.

Target Market(s)

Men and Women

Industry/Entity Type

psychology

Number of Pages Required

1 page

Requirements
Must have
• An "Online Training" Menu that includes links to "Chart your Daily Rhythm" , "Lantern and Compass Workbook," "Bright Morning Program" "Should We Dance Before Dawn" "Building Quiet Harmony"

```html
<!DOCTYPE html>
<html lang="en">
<head>
<meta charset="utf-8">
<title>Tovelane – Psychology Solutions</title>
<link rel="stylesheet" href="https://fonts.googleapis.com/css2?family=Poppins:wght@600;700;800&family=Montserrat:wght@400;500;600;700&display=swap">
<style>
:root{
  --teal:#1b93b5;
  --teal-dark:#137a98;
  --red:#d0202a;
  --navy:#0d3a5c;
  --ink:#2b2b2b;
  --grey:#5e6570;
  --pale:#edf2f8;
  --white:#ffffff;
}
*{margin:0;padding:0;box-sizing:border-box}
html,body{width:1200px;height:4622px;overflow:hidden}
body{position:relative;font-family:'Montserrat',sans-serif;color:var(--ink);background:var(--white)}
.abs{position:absolute}
h1,h2,h3{font-family:'Poppins',sans-serif;font-weight:700}
.btn{position:absolute;display:inline-flex;align-items:center;justify-content:center;font-family:'Montserrat',sans-serif;font-weight:700;font-size:12px;letter-spacing:.3px;text-transform:uppercase;border-radius:24px;text-decoration:none}
.btn-outline{border:2px solid var(--red);color:var(--red);width:152px;height:38px}
.btn-outline-light{border:2px solid var(--white);color:var(--white);width:152px;height:38px}
.photo{position:absolute}

/* header */
.site-header{position:absolute;left:0;top:0;width:1200px;height:80px;background:var(--white);box-shadow:0 1px 4px rgba(0,0,0,.06);z-index:5}
.brand{position:absolute;display:flex;align-items:center;gap:8px}
.brand-dot{width:22px;height:22px;border-radius:50%;background:var(--teal)}
.brand-name{font-family:'Montserrat',sans-serif;font-weight:700;font-size:18px;color:var(--teal)}
.main-nav{position:absolute;left:340px;top:0;height:80px;display:flex;align-items:center;gap:40px;font-size:14px;font-weight:700;color:var(--ink)}
.main-nav .active{position:relative}
.main-nav .active::after{content:"";position:absolute;left:0;bottom:-9px;width:40px;height:2px;background:var(--teal)}
.nav-book{position:absolute;left:966px;top:22px;width:112px;height:36px;border-radius:20px;background:var(--red);color:var(--white);font-size:14px;font-weight:700;display:flex;align-items:center;justify-content:center}

/* hero */
.hero{position:absolute;left:0;top:80px;width:1200px;height:720px;overflow:hidden}
.hero-photo{left:0;top:0;width:1200px;height:720px;background:linear-gradient(180deg,#bcd3df 0%,#d9dcd5 35%,#e8c796 58%,#d59a5a 72%,#8a8a86 100%)}
.hero-kicker{left:104px;top:198px;font-family:'Montserrat',sans-serif;font-weight:500;font-size:28px;letter-spacing:1.5px;color:var(--teal)}
.hero-title{left:102px;top:236px;font-size:44px;line-height:50px;color:#333;font-weight:700}
.hero .btn{left:102px;top:358px;width:218px;height:46px;background:var(--red);color:var(--white);font-size:13px}
.hero-dots{left:1160px;top:230px;display:flex;flex-direction:column;gap:9px}
.hero-dots span{width:10px;height:10px;border-radius:50%;background:var(--teal)}
.hero-dots span:first-child{background:transparent;border:2px solid var(--teal)}
.hero-cut{left:0;top:0}

/* about */
.about{position:absolute;left:0;top:800px;width:1200px;height:552px;background:linear-gradient(180deg,#ffffff 0%,#f7f3ee 40%,#ece3d6 100%)}
.frame-teal{left:110px;top:70px;width:200px;height:124px;border-left:12px solid var(--teal);border-top:12px solid var(--teal)}
.frame-red{left:295px;top:250px;width:252px;height:229px;border-right:12px solid var(--red);border-bottom:12px solid var(--red)}
.about-photo{left:130px;top:90px;width:392px;height:360px;background:linear-gradient(160deg,#d9dbd7,#b9a797 55%,#8a7a70)}
.section-title{font-size:34px;line-height:42px;color:var(--teal)}
.title-rule{position:absolute;width:46px;height:3px;background:var(--navy)}
.about .section-title{left:615px;top:90px}
.about .title-rule{left:617px;top:186px}
.body-copy{position:absolute;font-size:15px;line-height:29.5px;color:var(--grey)}
.about .body-copy{left:618px;top:218px;width:478px}
.about .btn{left:614px;top:403px}

/* intro */
.intro{position:absolute;left:0;top:1352px;width:1200px;height:568px;background:var(--pale);overflow:hidden}
.intro-photo{left:0;top:0;width:1200px;height:568px;background:linear-gradient(135deg,#c9bfae,#8a8e92 55%,#5e5a56);clip-path:polygon(710px 0,1200px 0,1200px 568px,550px 568px)}
.intro .section-title{left:146px;top:100px;font-size:38px;line-height:44px}
.intro .title-rule{left:148px;top:194px}
.intro .body-copy{left:148px;top:215px;width:438px;color:#4d535b}
.intro .btn{left:146px;top:418px}

/* services */
.services{position:absolute;left:0;top:1920px;width:1200px;height:480px;background:var(--white)}
.services .section-title{left:0;top:60px;width:1200px;text-align:center;font-size:38px}
.services .title-rule{left:576px;top:118px}
.service-card{position:absolute;top:160px;width:228px;height:296px;overflow:hidden}
.service-card .photo{left:0;top:0;width:228px;height:296px}
.service-label{position:absolute;left:0;bottom:20px;width:228px;text-align:center;color:var(--white);font-size:12.5px;font-weight:700;line-height:18px;text-transform:uppercase}
.card-offer{background:var(--red);color:var(--white);text-align:center;padding:52px 22px 0}
.card-offer h3{font-family:'Montserrat',sans-serif;font-size:13px;line-height:19px;font-weight:700;text-transform:uppercase}
.card-offer p{margin-top:10px;font-size:9px;line-height:14.5px;opacity:.92}
.card-offer .btn{position:static;margin:16px auto 0;width:110px;height:26px;border:2px solid var(--white);color:var(--white);font-size:8px}
.arrow{position:absolute;top:300px}

/* support */
.support{position:absolute;left:0;top:2396px;width:1200px;height:676px;background:var(--navy);overflow:hidden;clip-path:polygon(0 12px,1200px 0,1200px 676px,0 676px)}
.support-photo{left:0;top:0;width:1200px;height:676px;background:linear-gradient(90deg,#8c7a66 0%,#6d6a63 30%,#3c4c5d 52%,#0e3a5c 68%,#0b3558 100%)}
.support .section-title{left:615px;top:200px;color:var(--white)}
.support .body-copy{left:618px;top:324px;width:470px;color:#e4ecf3}
.support .body-copy p+p{margin-top:8px}
.support .btn{left:615px;top:540px}

/* online training */
.training{position:absolute;left:0;top:3072px;width:1200px;height:558px;background:var(--white);overflow:hidden}
.training-photo{left:380px;top:0;width:820px;height:558px;background:linear-gradient(90deg,rgba(255,255,255,1) 0%,rgba(236,236,232,.6) 20%,#dedcd6 45%,#c9c3b8 80%,#b0a89a 100%)}
.training .section-title{left:150px;top:88px;font-size:38px}
.training-sub{left:152px;top:150px;width:380px;font-size:20px;line-height:30px;color:#4c5259}
.training-list{position:absolute;left:152px;top:232px;list-style:none}
.training-list li{display:flex;align-items:center;gap:10px;height:34px;font-size:15.5px;font-weight:500;color:#333}
.training .btn{left:148px;top:432px}

/* courses */
.courses{position:absolute;left:0;top:3630px;width:1200px;height:620px;background:linear-gradient(180deg,#ffffff 0%,#f3ede4 30%,#e9dfd0 100%)}
.courses .section-title{left:0;top:80px;width:1200px;text-align:center;font-size:38px}
.courses .title-rule{left:576px;top:138px}
.course-card{position:absolute;top:160px;width:298px;height:312px}
.course-card .photo{left:0;top:0;width:298px;height:226px}
.course-box{position:absolute;left:28px;top:184px;width:262px;height:128px;background:var(--teal);border-radius:0 0 12px 12px;text-align:center;color:var(--white);padding-top:34px}
.course-box h3{font-family:'Montserrat',sans-serif;font-size:12.5px;line-height:19px;font-weight:700}
.course-box .btn{position:static;margin:14px auto 0;width:116px;height:26px;border:2px solid var(--white);color:var(--white);font-size:8px}

/* footer */
.site-footer{position:absolute;left:0;top:4250px;width:1200px;height:372px;background:var(--white)}
.socials{position:absolute;left:160px;top:132px;display:flex;gap:12px}
.socials span{width:30px;height:30px;border:2px solid var(--teal);border-radius:50%}
.footer-col{position:absolute;top:62px}
.footer-col h3{font-family:'Poppins',sans-serif;font-size:17px;color:var(--navy);margin-bottom:14px}
.footer-col li{list-style:none;font-size:12px;line-height:26px;color:#4a5058}
.contact-row{display:flex;align-items:center;gap:12px;font-size:12px;line-height:17px;color:#4a5058;margin-bottom:14px}
.contact-icon{flex:none;width:26px;height:26px;border-radius:50%;background:var(--teal);display:flex;align-items:center;justify-content:center}
.footer-rule{position:absolute;left:58px;top:298px;width:990px;height:1px;background:#d8dbe0}
.copyright{position:absolute;left:0;top:322px;width:1200px;text-align:center;font-size:12px;color:#5b6168}
</style>
</head>
<body>

<header class="site-header">
  <div class="brand" style="left:116px;top:28px"><span class="brand-dot"></span><span class="brand-name">Tovelane</span></div>
  <nav class="main-nav">
    <span class="active">Home</span><span>About</span><span>Services &amp; Fees</span><span>Online Training</span><span>Blog</span><span>Contact</span>
  </nav>
  <span class="nav-book">Bookings</span>
</header>

<section class="hero">
  <div class="photo hero-photo" role="img" aria-label="Family of four holding hands and running through shallow surf at sunset"></div>
  <p class="abs hero-kicker">Tovelane</p>
  <h1 class="abs hero-title">Psychology Solutions<br>+ Your Choices</h1>
  <a class="btn">Book Appointment</a>
  <div class="abs hero-dots"><span></span><span></span><span></span><span></span></div>
  <svg class="abs hero-cut" width="1200" height="720" viewBox="0 0 1200 720">
    <polygon points="0,583 600,712 1200,557 1200,575 600,722 0,602" fill="#d0202a"/>
    <polygon points="0,602 600,722 1200,575 1200,720 0,720" fill="#ffffff"/>
  </svg>
</section>

<section class="about">
  <div class="abs frame-teal"></div>
  <div class="abs frame-red"></div>
  <div class="photo about-photo" role="img" aria-label="Portrait of the psychologist smiling on a beach background"></div>
  <h2 class="abs section-title">About experienced Gold<br>Coast Psychologist</h2>
  <span class="title-rule"></span>
  <p class="body-copy">Unfortunately, we all go through periods of crisis in our lives. When we find ourselves struggling for an extended period, we can use bit of help to work through barriers that stand in our way. Counselling or psychotherapy can help. Contact Daniel, your Gold Coast Psychologist.</p>
  <a class="btn btn-outline">Learn More</a>
</section>

<section class="intro">
  <div class="photo intro-photo" role="img" aria-label="Couple embracing on a sofa during a counselling session while a therapist takes notes"></div>
  <h2 class="abs section-title">Tovelane by<br>Daniel Hartley</h2>
  <span class="title-rule"></span>
  <p class="body-copy">Congratulations on taking the first step to overcoming your barriers and being who you want to be. At Tovelane, we are focused on your mental wellness. Tovelane is open to anyone looking for a Gold Coast Psychologist or online therapist to help them overcome barriers and find fulfillment in their lives.</p>
  <a class="btn btn-outline">Learn More</a>
</section>

<section class="services">
  <h2 class="abs section-title">Services Provide</h2>
  <span class="title-rule"></span>
  <svg class="arrow" style="left:78px" width="20" height="32" viewBox="0 0 20 32"><polyline points="16,3 4,16 16,29" fill="none" stroke="#1b93b5" stroke-width="4"/></svg>
  <div class="service-card" style="left:120px">
    <div class="photo" role="img" aria-label="Couple seated together in a counselling session" style="background:linear-gradient(180deg,#c9c7c2,#8e8478 60%,#3f3a36)"></div>
    <p class="service-label">Psychological<br>Counselling</p>
  </div>
  <div class="service-card card-offer" style="left:358px">
    <h3>Self Esteem Course<br>Only $47</h3>
    <p>Lorem ipsum dolor sit amet, consectetur adipiscing elit, sed do eiusmod tempor incididunt ut labore et dolore magna aliqua. Quis ipsum gravida, risus commodo viverra maecenas accumsan lacus facilisis.</p>
    <a class="btn">Learn More</a>
  </div>
  <div class="service-card" style="left:596px">
    <div class="photo" role="img" aria-label="Man watching an online webinar on a laptop" style="background:linear-gradient(180deg,#d8cdb8,#a57f55 55%,#3b342d)"></div>
    <p class="service-label">Free Self Esteem<br>Webinar</p>
  </div>
  <div class="service-card" style="left:834px">
    <div class="photo" role="img" aria-label="Couple completing a quiz together on a laptop" style="background:linear-gradient(180deg,#c4c6c3,#8f7c69 55%,#3a3531)"></div>
    <p class="service-label">Free<br>Assertiveness Quiz</p>
  </div>
  <svg class="arrow" style="left:1082px" width="20" height="32" viewBox="0 0 20 32"><polyline points="4,3 16,16 4,29" fill="none" stroke="#1b93b5" stroke-width="4"/></svg>
</section>

<section class="support">
  <div class="photo support-photo" role="img" aria-label="Smiling couple sitting close together on a sofa"></div>
  <h2 class="abs section-title">About experienced Gold<br>Coast Psychologist</h2>
  <div class="body-copy">
    <p>Wondering where to start? Watch our free Self Worth Webinar. Wondering how your self Esteem stacks up? take our Assertiveness Quiz. Interested in a what psychotherapy can offer but not quite ready? Try our Self Esteem Course</p>
    <p>Your Online or Gold Coast Psychologist should not only be about moving away from what makes you sad</p>
  </div>
  <a class="btn btn-outline-light">Learn More</a>
</section>

<section class="training">
  <div class="photo training-photo" role="img" aria-label="Man with glasses smiling while working on a laptop"></div>
  <h2 class="abs section-title">Online Training</h2>
  <p class="abs training-sub">Gold Coast Psychologist Also offering Australia-wide telehealth</p>
  <ul class="training-list">
    <li><svg width="16" height="14" viewBox="0 0 16 14"><polyline points="2,7 6,11 14,2" fill="none" stroke="#1b93b5" stroke-width="2.5"/></svg>Chart your Daily Rhythm</li>
    <li><svg width="16" height="14" viewBox="0 0 16 14"><polyline points="2,7 6,11 14,2" fill="none" stroke="#1b93b5" stroke-width="2.5"/></svg>Lantern and Compass Workbook</li>
    <li><svg width="16" height="14" viewBox="0 0 16 14"><polyline points="2,7 6,11 14,2" fill="none" stroke="#1b93b5" stroke-width="2.5"/></svg>Bright Morning Program</li>
    <li><svg width="16" height="14" viewBox="0 0 16 14"><polyline points="2,7 6,11 14,2" fill="none" stroke="#1b93b5" stroke-width="2.5"/></svg>Should We Dance Before Dawn</li>
    <li><svg width="16" height="14" viewBox="0 0 16 14"><polyline points="2,7 6,11 14,2" fill="none" stroke="#1b93b5" stroke-width="2.5"/></svg>Building Quiet Harmony</li>
  </ul>
  <a class="btn btn-outline">Learn More</a>
</section>

<section class="courses">
  <h2 class="abs section-title">Upcoming Courses</h2>
  <span class="title-rule"></span>
  <div class="course-card" style="left:138px">
    <div class="photo" role="img" aria-label="Group of adults talking together in a workshop" style="background:linear-gradient(180deg,#dfe3e4,#8f8a84 60%,#4a4440)"></div>
    <div class="course-box"><h3>Lorem ipsum dolor sit amet,<br>consectetur adipiscin</h3><a class="btn">Learn More</a></div>
  </div>
  <div class="course-card" style="left:462px">
    <div class="photo" role="img" aria-label="Facilitator leading a seated group discussion" style="background:linear-gradient(180deg,#e5e2dc,#a89684 60%,#4d4540)"></div>
    <div class="course-box"><h3>Lorem ipsum dolor sit amet,<br>consectetur adipiscin</h3><a class="btn">Learn More</a></div>
  </div>
  <div class="course-card" style="left:785px">
    <div class="photo" role="img" aria-label="Small group therapy session with a folder of notes" style="background:linear-gradient(180deg,#d9dcd8,#8c8276 60%,#3f3a36)"></div>
    <div class="course-box"><h3>Lorem ipsum dolor sit amet,<br>consectetur adipiscin</h3><a class="btn">Learn More</a></div>
  </div>
</section>

<footer class="site-footer">
  <div class="brand" style="left:152px;top:78px"><span class="brand-dot"></span><span class="brand-name">Tovelane</span></div>
  <div class="socials"><span></span><span></span><span></span><span></span></div>
  <div class="footer-col" style="left:416px">
    <h3>Daniel Hartley</h3>
    <ul><li>Registered Psychologist</li><li>CPSA</li><li>CLCA Accredited Life Coach</li><li>TRTA Full Member</li></ul>
  </div>
  <div class="footer-col" style="left:663px">
    <h3>Links</h3>
    <ul><li>Home</li><li>About Us</li><li>Services &amp; Fees</li><li>Book Today</li></ul>
  </div>
  <div class="footer-col" style="left:850px">
    <h3>Contact Us</h3>
    <div class="contact-row"><span class="contact-icon"><svg width="12" height="14" viewBox="0 0 12 14"><path d="M6 0a5 5 0 0 0-5 5c0 4 5 9 5 9s5-5 5-9a5 5 0 0 0-5-5zm0 7a2 2 0 1 1 0-4 2 2 0 0 1 0 4z" fill="#fff"/></svg></span>48 Harbour Lane, Seabrook</div>
    <div class="contact-row"><span class="contact-icon"><svg width="12" height="12" viewBox="0 0 12 12"><path d="M2.5 0.5l2 2.5-1.2 1.5a7 7 0 0 0 4.2 4.2L9 7.5l2.5 2-1 2C5 11.5 0.5 7 0.5 1.5z" fill="#fff"/></svg></span><span>0400 000 123<br>Fax. (07) 5550 0199</span></div>
    <div class="contact-row"><span class="contact-icon"><svg width="14" height="14" viewBox="0 0 14 14"><circle cx="7" cy="7" r="5.5" fill="none" stroke="#fff" stroke-width="1.6"/><polyline points="7,4 7,7 9,8.5" fill="none" stroke="#fff" stroke-width="1.6"/></svg></span>8:00am – 7:00pm (appt. Only)</div>
  </div>
  <div class="footer-rule"></div>
  <p class="copyright">© 2024 Company Name | All Rights Reserved</p>
</footer>

</body>
</html>
```